Business Card Design

Business Card for professional consulting firm working with large financial institutions.

Target Market(s)

Executive buyers

Industry/Entity Type

Banking

Contact Information for Business Card

Mild creativity wanted. Not boring, but do elaborate artwork.

Font styles to use
Serif
Sans Serif

Colors

Designer to choose colors to be used in the design.

Requirements
Must have
• Standard business card features - company name, individual name, telephone, website, email, locations.
Nice to have
• Two colors
Should not have
• too many colors, fancy printing, cartoons.

```html
<!DOCTYPE html>
<html lang="en">
<head>
<meta charset="utf-8">
<title>m7advisors business card</title>
<link href="https://fonts.googleapis.com/css2?family=Roboto:wght@400;700&display=swap" rel="stylesheet">
<style>
  :root {
    --ink: #0b0b0b;
    --paper: #ffffff;
    --rim: #c9c9c9;
    --rim-dark: #a9a9a9;
    --name: #3a3a3a;
    --muted: #a4a4a4;
    --detail: #6a6a6a;
    --backdrop: #e7e4df;
    --reverse-text: #ffffff;
  }
  * { margin: 0; padding: 0; box-sizing: border-box; }
  html, body { width: 1200px; height: 950px; overflow: hidden; }
  body { background: var(--backdrop); position: relative; font-family: "Roboto", Arial, sans-serif; }

  .card {
    position: absolute;
    width: 600px;
    height: 343px;
    overflow: hidden;
    box-shadow: 0 10px 30px rgba(0,0,0,0.18);
  }
  .card--front { left: 60px; top: 80px; background: var(--ink); }
  .card--back  { left: 540px; top: 527px; background: var(--ink); }

  .front-shape { position: absolute; inset: 0; width: 100%; height: 100%; }

  .brand-name {
    position: absolute;
    font-family: "Roboto", Arial, sans-serif;
    font-weight: 400;
    white-space: nowrap;
  }
  .card--front .brand-name {
    left: 250px; top: 62px; width: 240px;
    text-align: center; font-size: 30px; color: var(--ink);
  }
  .card--back .brand-name {
    left: 0; right: 0; top: 50%; transform: translateY(-50%);
    text-align: center; font-size: 56px; color: var(--reverse-text);
  }

  .contact { position: absolute; left: 118px; bottom: 42px; }
  .contact__name { font-size: 17px; font-weight: 700; color: var(--name); letter-spacing: 0.4px; }
  .contact__role { font-size: 12px; color: var(--muted); letter-spacing: 0.6px; margin-bottom: 10px; }
  .contact__address { font-size: 12px; color: var(--detail); line-height: 1.35; margin-bottom: 4px; }
  .contact__line { display: flex; align-items: center; gap: 7px; font-size: 12px; color: var(--detail); line-height: 1.5; }
  .contact__icon { width: 10px; height: 10px; fill: var(--ink); flex: none; }
</style>
</head>
<body>

  <section class="card card--front" aria-label="Business card front">
    <svg class="front-shape" viewBox="0 0 600 343" aria-hidden="true">
      <ellipse cx="300" cy="171" rx="318" ry="214" fill="var(--rim-dark)"/>
      <ellipse cx="304" cy="167" rx="312" ry="208" fill="var(--rim)"/>
      <ellipse cx="308" cy="163" rx="304" ry="202" fill="var(--paper)"/>
    </svg>

    <div class="brand-name">m7advisors</div>

    <div class="contact">
      <div class="contact__name">DANIEL REYES</div>
      <div class="contact__role">CEO/FOUNDER</div>
      <div class="contact__address">1420 Harbor View Road<br>Fairbanks, Alaska 99712</div>
      <div class="contact__line">
        <svg class="contact__icon" viewBox="0 0 10 10" aria-hidden="true"><path d="M2 0.5 L3.6 2.8 L2.7 3.8 Q3.8 6 6.2 7.3 L7.2 6.4 L9.5 8 L8.4 9.5 Q4.5 9.3 1.6 5.8 Q0.3 3.8 0.6 1.6 Z"/></svg>
        <span>907 555 0184</span>
      </div>
      <div class="contact__line">
        <svg class="contact__icon" viewBox="0 0 10 10" aria-hidden="true"><path d="M0 2 H10 V8.5 H0 Z M0.6 2.4 L5 5.8 L9.4 2.4" stroke="#fff" stroke-width="0.8"/></svg>
        <span>info@m7advisors.com</span>
      </div>
      <div class="contact__line">
        <svg class="contact__icon" viewBox="0 0 10 10" aria-hidden="true"><circle cx="5" cy="5" r="4.6"/></svg>
        <span>www.m7advisors.com</span>
      </div>
    </div>
  </section>

  <section class="card card--back" aria-label="Business card back">
    <div class="brand-name">m7advisors</div>
  </section>

</body>
</html>
```